DL Cards to get buyers attention

I’m looking to have four double-sided DL flyers professionally prepared and made print-ready in high resolution.

I have uploaded the four existing designs, and I’m happy for them to be reviewed with a fresh set of eyes. While I’m generally happy with the direction, I’m very open to recommendations around layout, typography, imagery, colour balance, spacing and overall presentation if there are opportunities to create a stronger and more professional result.

The key objective is to develop a consistent and recognisable suite of marketing material that strengthens both Lon Pakard brand awareness and my personal profile in the local real estate market. Each flyer should feel like part of the same campaign while still having its own clear message and purpose.

I want the finished designs to feel professional, confident, modern and premium, without becoming overly busy or losing the simplicity that makes a DL flyer easy to read. Strong headlines, clear messaging and an obvious call to action are important. The Lon Pakard branding should be immediately recognisable, while my photograph, name and contact details should be incorporated naturally and consistently.

Please review the existing designs and suggest any changes that would improve their visual impact, readability and consistency. I’m also open to seeing an alternative design direction if you believe there is a better overall look.

The final artwork needs to be supplied professionally print-ready at DL size (210 mm × 99 mm), double-sided, high resolution, CMYK where appropriate, with 3 mm bleed and safe margins, so it can be provided directly to a commercial printer.

The overall goal is simple: strong branding, professional presentation, consistent recognition and marketing material that people will remember.

Target Market(s)

People looking at selling their homes

Industry/Entity Type

Real Estate

Font styles to use
Serif
Sans Serif

Requirements
Must have
• Strong brand awareness - Lon Pakard
Nice to have
• bright and fresh

```html
<!DOCTYPE html>
<html lang="en">
<head>
<meta charset="utf-8">
<title>Lon Pakard – DL Flyer Suite</title>
<link href="https://fonts.googleapis.com/css2?family=Montserrat:wght@400;500;600;700;800&family=Dancing+Script:wght@500;600&display=swap" rel="stylesheet">
<style>
  :root {
    --brand-yellow: #f2c631;
    --ink: #0d0d0d;
    --paper: #ffffff;
    --backdrop: #a29a95;
    --muted: #333333;
    --sans: "Montserrat", Arial, sans-serif;
    --script: "Dancing Script", cursive;
  }
  * { box-sizing: border-box; margin: 0; padding: 0; }
  html, body { width: 1200px; height: 1029px; overflow: hidden; }
  body { background: var(--backdrop); font-family: var(--sans); color: var(--ink); position: relative; }

  .flyer {
    position: absolute; left: 131px; width: 937px; height: 441px;
    background: var(--paper); overflow: hidden;
    box-shadow: 0 6px 14px rgba(0,0,0,.35);
  }
  .flyer--sell { top: 36px; }
  .flyer--ready { top: 551px; }
  .abs { position: absolute; }

  .brand-box {
    position: absolute; left: 44px; top: 0; width: 105px; height: 56px;
    background: var(--brand-yellow); display: flex; align-items: flex-end; justify-content: center;
    padding-bottom: 12px;
  }
  .brand-name { font-family: var(--sans); font-weight: 800; font-size: 17px; color: var(--ink); letter-spacing: -.3px; }

  .headline { font-weight: 800; line-height: 1; letter-spacing: -.3px; text-transform: uppercase; }
  .headline .accent { color: var(--brand-yellow); }

  .script { font-family: var(--script); font-weight: 600; color: var(--ink); }

  .photo { position: absolute; }

  .feature-title { font-weight: 700; font-size: 10px; text-transform: uppercase; letter-spacing: .2px; }
  .feature-text { font-size: 9px; line-height: 1.05; color: var(--muted); }
  .divider { position: absolute; width: 1.5px; background: var(--ink); }

  .footer-band { position: absolute; left: 0; top: 379px; height: 62px; background: var(--ink); }
  .value { position: absolute; display: flex; align-items: center; gap: 8px; color: var(--paper); }
  .value svg { flex: none; }
  .value-title { font-size: 6px; font-weight: 600; line-height: 1.4; }
  .value-text { font-size: 5.2px; line-height: 1.2; opacity: .9; }
  .footer-rule { position: absolute; width: 1.5px; background: var(--brand-yellow); }
  .tagline { position: absolute; font-family: var(--script); color: var(--brand-yellow); font-size: 14px; line-height: .95; transform: rotate(-4deg); }
  .tagline::after { content: ""; display: block; width: 78px; height: 1.5px; background: var(--paper); margin-top: 4px; border-radius: 2px; }

  .cta-panel { position: absolute; }
  .cta-title { position: absolute; font-weight: 800; color: var(--ink); text-transform: uppercase; letter-spacing: .3px; line-height: 1; }
  .cta-phone {
    position: absolute; background: var(--paper); border-radius: 8px;
    font-weight: 700; color: var(--ink); display: flex; align-items: center; justify-content: center; letter-spacing: .5px;
  }
  .cta-phone::before {
    content: ""; position: absolute; left: -6px; top: -5px; width: 18px; height: 12px;
    background: var(--paper); clip-path: polygon(0 0, 100% 45%, 70% 100%);
  }
  .phone-badge { position: absolute; border-radius: 50%; background: var(--ink); display: flex; align-items: center; justify-content: center; }
</style>
</head>
<body>

<!-- Flyer 1: The smart way to sell -->
<section class="flyer flyer--sell">
  <div class="photo" role="img" aria-label="Photo of a large white two-storey house among bare trees with the agent smiling in a white shirt"
       style="left:433px; top:0; width:504px; height:380px;
       background: linear-gradient(90deg, #fff 0%, rgba(255,255,255,0) 28%),
                   linear-gradient(180deg, #b9b4ae 0%, #8e8f8a 45%, #c9cdd2 70%, #6e7a55 100%);"></div>

  <div class="brand-box"><span class="brand-name">Lon Pakard</span></div>

  <h1 class="headline abs" style="left:44px; top:78px; font-size:31px;">The smart way<br>to sell your</h1>
  <div class="headline abs accent" style="left:44px; top:146px; font-size:44px; color:var(--brand-yellow);">Property</div>
  <div class="script abs" style="left:48px; top:192px; font-size:28px; transform:rotate(-3deg);">Start with knowledge.</div>
  <svg class="abs" style="left:165px; top:226px;" width="122" height="10" viewBox="0 0 122 10"><path d="M2 7 Q60 1 120 4" stroke="var(--brand-yellow)" stroke-width="2.2" fill="none" stroke-linecap="round"/></svg>

  <p class="abs" style="left:50px; top:236px; font-size:13px; line-height:1.05;">Before you put your property on the market,<br><strong style="font-weight:700;">know what needs attention.</strong></p>

  <div class="abs" style="left:46px; top:280px; width:34px; height:34px; border:1.5px solid var(--brand-yellow); border-radius:50%; display:flex; align-items:center; justify-content:center;">
    <svg width="18" height="17" viewBox="0 0 24 22"><path d="M12 1 1 11h3v10h6v-6h4v6h6V11h3z" fill="var(--ink)"/></svg>
  </div>
  <div class="feature-title abs" style="left:46px; top:322px;">Know</div>
  <p class="feature-text abs" style="left:46px; top:340px; font-size:9.5px;">Identify potential<br>issues early.</p>

  <div class="divider" style="left:155px; top:301px; height:60px;"></div>

  <div class="abs" style="left:179px; top:283px; width:34px; height:34px; border:1.5px solid var(--brand-yellow); border-radius:50%; display:flex; align-items:center; justify-content:center;">
    <svg width="15" height="19" viewBox="0 0 16 20"><rect x="1" y="2" width="14" height="17" rx="1.5" fill="none" stroke="var(--ink)" stroke-width="1.3"/><rect x="5" y="0.5" width="6" height="3" rx="1" fill="var(--ink)"/><path d="M4 8h8M4 11h8M4 14h8" stroke="var(--ink)" stroke-width="1.1"/></svg>
  </div>
  <div class="feature-title abs" style="left:179px; top:324px;">Prepare</div>
  <p class="feature-text abs" style="left:179px; top:342px; font-size:9.5px;">Make informed<br>improvements.</p>

  <div class="divider" style="left:282px; top:301px; height:60px;"></div>

  <div class="abs" style="left:300px; top:283px; width:34px; height:34px; border:1.5px solid var(--brand-yellow); border-radius:50%; display:flex; align-items:center; justify-content:center;">
    <svg width="20" height="14" viewBox="0 0 26 18"><circle cx="13" cy="5" r="3.5" fill="var(--ink)"/><circle cx="5" cy="7" r="2.7" fill="var(--ink)"/><circle cx="21" cy="7" r="2.7" fill="var(--ink)"/><path d="M6.5 17c0-4 3-6.5 6.5-6.5s6.5 2.5 6.5 6.5z" fill="var(--ink)"/><path d="M0 17c0-3 2-5 5-5 1.5 0 2.4.5 3 1-1 1.2-1.6 2.5-1.6 4zM26 17c0-3-2-5-5-5-1.5 0-2.4.5-3 1 1 1.2 1.6 2.5 1.6 4z" fill="var(--ink)"/></svg>
  </div>
  <div class="feature-title abs" style="left:300px; top:324px;">Sell</div>
  <p class="feature-text abs" style="left:300px; top:342px; font-size:9.5px;">Attract more<br>confident buyers.</p>

  <div class="footer-band" style="width:600px;"></div>
  <div class="tagline" style="left:44px; top:392px;">Your property<br>Our priority</div>
  <div class="footer-rule" style="left:145px; top:396px; height:30px;"></div>
  <div class="value" style="left:160px; top:396px;">
    <svg width="30" height="28" viewBox="0 0 30 28"><path d="M3 13 15 2l12 11M6 11v16h7v-9h4v9h7V11" fill="none" stroke="var(--brand-yellow)" stroke-width="1.6" stroke-linejoin="round"/></svg>
    <div><div class="value-title">Local Knowledge.</div><div class="value-text">We know the area<br>and the market</div></div>
  </div>
  <div class="footer-rule" style="left:265px; top:396px; height:30px;"></div>
  <div class="value" style="left:277px; top:398px;">
    <svg width="34" height="24" viewBox="0 0 34 24"><g fill="none" stroke="var(--brand-yellow)" stroke-width="1.4"><circle cx="17" cy="7" r="5"/><circle cx="7" cy="10" r="4"/><circle cx="27" cy="10" r="4"/><path d="M8 23c0-5 4-9 9-9s9 4 9 9M1 22c0-4 2-7 6-7M33 22c0-4-2-7-6-7"/></g></svg>
    <div><div class="value-title">Exceptional Service.</div><div class="value-text">Focused on achieving<br>the best results.</div></div>
  </div>
  <div class="footer-rule" style="left:385px; top:396px; height:30px;"></div>
  <div class="value" style="left:399px; top:400px;">
    <svg width="24" height="21" viewBox="0 0 24 21"><path d="M12 20 2.5 10.5A5.5 5.5 0 0 1 12 3.5a5.5 5.5 0 0 1 9.5 7z" fill="none" stroke="var(--brand-yellow)" stroke-width="1.5" stroke-linejoin="round"/></svg>
    <div><div class="value-title">Genuine Care.</div><div class="value-text">Your goals are our<br>priority.</div></div>
  </div>

  <svg class="cta-panel" style="left:540px; top:321px;" width="397" height="120" viewBox="0 0 397 120"><path d="M87 0H397V120H7L70 10Q76 0 87 0z" fill="var(--brand-yellow)"/></svg>
  <div class="cta-title" style="left:714px; top:338px; font-size:29px;">Call Sam</div>
  <div class="phone-badge" style="left:628px; top:373px; width:48px; height:48px;">
    <svg width="24" height="24" viewBox="0 0 24 24"><path d="M6.6 10.8a15 15 0 0 0 6.6 6.6l2.2-2.2c.3-.3.7-.4 1-.2 1.1.4 2.3.6 3.6.6.6 0 1 .4 1 1V20c0 .6-.4 1-1 1A17 17 0 0 1 3 4c0-.6.4-1 1-1h3.5c.6 0 1 .4 1 1 0 1.3.2 2.5.6 3.6.1.3 0 .7-.2 1z" fill="var(--paper)"/></svg>
  </div>
  <div class="cta-phone" style="left:710px; top:376px; width:182px; height:45px; font-size:21px;">0400 123 456</div>
</section>

<!-- Flyer 2: 3 ways to get market-ready -->
<section class="flyer flyer--ready">
  <div class="photo" role="img" aria-label="Portrait of the agent smiling in a white shirt against a soft blurred outdoor background"
       style="left:684px; top:0; width:253px; height:380px; border-left:1px solid var(--brand-yellow);
       background: linear-gradient(180deg, #ffffff 0%, #f3f3f1 35%, #d8dbd6 65%, #c5cbbf 100%);"></div>

  <h1 class="headline abs" style="left:44px; top:48px; font-size:30px;">3 ways to get your</h1>
  <div class="headline abs" style="left:46px; top:88px; font-size:63px; color:var(--brand-yellow);">Property</div>
  <div class="headline abs" style="left:44px; top:146px; font-size:40px;">Market-ready</div>
  <div class="abs" style="left:44px; top:193px; width:83px; height:3px; background:var(--brand-yellow);"></div>

  <p class="abs" style="left:44px; top:208px; font-size:12.2px; line-height:1.2; color:var(--muted);">Preparing your property before you sell can help attract more<br>buyers and achieve a better result.</p>

  <div class="script abs" style="left:450px; top:100px; font-size:30px; line-height:1.2; transform:rotate(-10deg); font-weight:500;">Ready to make<br>&nbsp;your next move?</div>
  <svg class="abs" style="left:505px; top:162px;" width="140" height="30" viewBox="0 0 140 30"><path d="M3 27 Q60 8 138 5" stroke="var(--brand-yellow)" stroke-width="2.4" fill="none" stroke-linecap="round"/></svg>

  <svg class="abs" style="left:88px; top:262px;" width="30" height="28" viewBox="0 0 24 22"><path d="M12 1 1 11h3v10h6v-6h4v6h6V11h3z" fill="var(--ink)"/></svg>
  <div class="feature-title abs" style="left:0; width:205px; text-align:center; top:300px;">Get things fixed</div>
  <p class="feature-text abs" style="left:45px; width:110px; text-align:center; top:328px; font-size:6.4px; line-height:1.25;">Address issues that could affect your property's presentation, condition or appeal before marketing.</p>

  <div class="divider" style="left:171px; top:278px; height:82px;"></div>

  <svg class="abs" style="left:236px; top:258px;" width="24" height="32" viewBox="0 0 16 20"><rect x="1" y="2" width="14" height="17" rx="1.5" fill="none" stroke="var(--ink)" stroke-width="1"/><rect x="5" y="0.5" width="6" height="3" rx="1" fill="var(--ink)"/><path d="M6 7h6M6 10h6M6 13h6M6 16h6M3.5 7h1M3.5 10h1M3.5 13h1M3.5 16h1" stroke="var(--ink)" stroke-width=".9"/></svg>
  <div class="feature-title abs" style="left:167px; width:160px; text-align:center; top:300px; line-height:1;">Know what<br>buyers will see</div>
  <p class="feature-text abs" style="left:187px; width:120px; text-align:center; top:328px; font-size:6.4px; line-height:1.25;">A professional inspection can identify potential concerns early, giving you the opportunity to deal with them before they become obstacles.</p>

  <div class="divider" style="left:313px; top:278px; height:82px;"></div>

  <svg class="abs" style="left:375px; top:265px;" width="30" height="21" viewBox="0 0 26 18"><circle cx="13" cy="5" r="3.5" fill="var(--ink)"/><circle cx="5" cy="7" r="2.7" fill="var(--ink)"/><circle cx="21" cy="7" r="2.7" fill="var(--ink)"/><path d="M6.5 17c0-4 3-6.5 6.5-6.5s6.5 2.5 6.5 6.5z" fill="var(--ink)"/><path d="M0 17c0-3 2-5 5-5 1.5 0 2.4.5 3 1-1 1.2-1.6 2.5-1.6 4zM26 17c0-3-2-5-5-5-1.5 0-2.4.5-3 1 1 1.2 1.6 2.5 1.6 4z" fill="var(--ink)"/></svg>
  <div class="feature-title abs" style="left:315px; width:160px; text-align:center; top:300px; line-height:1;">Give buyers<br>confidence</div>
  <p class="feature-text abs" style="left:333px; width:122px; text-align:center; top:328px; font-size:6.4px; line-height:1.25;">When buyers have better information about your property, they can make decisions with greater confidence.</p>

  <p class="abs" style="left:526px; top:275px; font-size:14px; line-height:1.45; font-weight:500;">Let's talk about<br><span style="font-weight:400;">your property.</span></p>

  <div class="footer-band" style="width:720px;"></div>
  <div class="brand-box" style="top:379px; height:52px; align-items:center; padding:0;"><span class="brand-name">Lon Pakard</span></div>
  <div class="value" style="left:171px; top:392px;">
    <svg width="36" height="33" viewBox="0 0 30 28"><path d="M3 13 15 2l12 11M6 11v16h7v-9h4v9h7V11" fill="none" stroke="var(--brand-yellow)" stroke-width="1.5" stroke-linejoin="round"/></svg>
    <div><div class="value-title">Local Knowledge.</div><div class="value-text" style="font-size:5.8px;">We know the area<br>and the market</div></div>
  </div>
  <div class="footer-rule" style="left:293px; top:395px; height:32px;"></div>
  <div class="value" style="left:305px; top:398px;">
    <svg width="38" height="26" viewBox="0 0 34 24"><g fill="none" stroke="var(--brand-yellow)" stroke-width="1.3"><circle cx="17" cy="7" r="5"/><circle cx="7" cy="10" r="4"/><circle cx="27" cy="10" r="4"/><path d="M8 23c0-5 4-9 9-9s9 4 9 9M1 22c0-4 2-7 6-7M33 22c0-4-2-7-6-7"/></g></svg>
    <div><div class="value-title">Exceptional Service.</div><div class="value-text" style="font-size:5.8px;">Focused on achieving<br>the best results.</div></div>
  </div>
  <div class="footer-rule" style="left:431px; top:395px; height:32px;"></div>
  <div class="value" style="left:446px; top:400px;">
    <svg width="27" height="24" viewBox="0 0 24 21"><path d="M12 20 2.5 10.5A5.5 5.5 0 0 1 12 3.5a5.5 5.5 0 0 1 9.5 7z" fill="none" stroke="var(--brand-yellow)" stroke-width="1.4" stroke-linejoin="round"/></svg>
    <div><div class="value-title">Genuine Care.</div><div class="value-text" style="font-size:5.8px;">Your goals are our<br>priority.</div></div>
  </div>
  <div class="footer-rule" style="left:560px; top:395px; height:32px;"></div>
  <div class="tagline" style="left:574px; top:390px;">Your property<br>Our priority</div>

  <svg class="cta-panel" style="left:660px; top:347px;" width="277" height="94" viewBox="0 0 277 94"><path d="M78 0H277V94H2L63 8Q68 0 78 0z" fill="var(--brand-yellow)"/></svg>
  <div class="cta-title" style="left:719px; top:368px; font-size:22px;">Call Sam</div>
  <div class="phone-badge" style="left:709px; top:394px; width:38px; height:38px;">
    <svg width="19" height="19" viewBox="0 0 24 24"><path d="M6.6 10.8a15 15 0 0 0 6.6 6.6l2.2-2.2c.3-.3.7-.4 1-.2 1.1.4 2.3.6 3.6.6.6 0 1 .4 1 1V20c0 .6-.4 1-1 1A17 17 0 0 1 3 4c0-.6.4-1 1-1h3.5c.6 0 1 .4 1 1 0 1.3.2 2.5.6 3.6.1.3 0 .7-.2 1z" fill="var(--paper)"/></svg>
  </div>
  <div class="cta-phone" style="left:773px; top:397px; width:139px; height:34px; font-size:15.5px;">0400 123 456</div>
</section>

</body>
</html>
```